Bright and beautiful business card for a coach

I'm a personal and business coach based in Perth, Australia. I need a business card that whilst subtle and elegant, will stand out and appeal on a table full of cards.

My business name is Fern Mentoring and the business card must represent the warmth and brightness implied in the name, without being gimmicky. It must have a warmth and appeal and be easy to read.

I prefer clean, minimalist designs.

It must align with the feel of my website and socials: https://www.fernmentoring-example.com.au/
https://www.instagram.com/fernmentoringau/
https://www.facebook.com/fernmentoringau
Updates

Hi Designers Thank you so much for taking the time to submit designs. I wonder if I could have explained myself a little better. Most of the designs that have been submitted look rather formal and many have quite corporate looking embellishments on them (to my eye). I would like softer, warmer, more organic. I’m open to people playing about and being more abstract, using softer embellishments (e.g the line drawing flowers and grasses I’ve used in my socials) incorporating other colours from my palette or like the social icons in my email signature (in PDF), perhaps playing with size/oversize, playing with the bleed. Please don’t be constrained by what I’ve already done, it merely needs to compliment. I’m sorry if I’m not using the right words or have led you astray. I’m no designer, but I’ve done my website, socials, email signature etc all myself (my logo was a design contest) and I was really hoping for my business card to be something more creative than I could have made with a template. Reminder: No black cards/sides please. Thank you 😊

Target Market(s)

Individuals, most likely but not all female. Creative thinkers. Likely professionals.

Industry/Entity Type

Business & Personal Coach

Contact Information for Business Card

(Fern Mentoring Logo) Name: Greta Pellham; Title: Business & Personal Coach; Phone number: +61 (0)458 913307; Email: greta@fernmentoring-example.com.au; Website: https://fernmentoring-example.com.au; Social icons for Facebook, Instagram & LinkedIn: @fernmentoringAU. Optional strapline: "A steady guide to help you find clarity in the clutter"

Font styles to use
Sans Serif

Colors
00AB8E
00BBA5
67D7C9
C6EFE9
E9F9F6
59FF00
82FF00
B8FF75
E3FFCB
F4FFEA
FFC000
F8CF3A
FAE287
FDF2CF
FEFAEE

Requirements
Must have
• Must align with feel of my website and socials. Must have a pop of #FFC000 (possibly whole of one side, or at least a block). Bright or white background. Easy to read.
Nice to have
• Possibly incorporate the sunshine/grass picture I have used in website and socials - will upload.
Should not have
• Must not be black or dark. Not impersonal or corporate looking.

```html
<!DOCTYPE html>
<html lang="en">
<head>
<meta charset="utf-8">
<title>Fern Mentoring – Business Card</title>
<link href="https://fonts.googleapis.com/css2?family=Arimo:wght@400;700&display=swap" rel="stylesheet">
<style>
  :root{
    --stage:#ece9e4;
    --grass-dark:#3f6a1c;
    --grass-mid:#6f9a2c;
    --sun-glow:#fff4d6;
    --band-orange:#d98414;
    --band-yellow:#f3c02b;
    --peach-deep:#f1b56a;
    --peach-soft:#fbe3c0;
    --cream:#fff8ee;
    --gold:#d38b12;
    --brown:#a8661a;
    --ink:#4d4740;
    --white:#ffffff;
  }
  *{box-sizing:border-box;margin:0;padding:0}
  html,body{width:1200px;height:900px;overflow:hidden}
  body{background:var(--stage);font-family:"Arimo",Arial,sans-serif;position:relative}

  .card{position:absolute;left:250px;width:700px;height:400px;border-radius:18px;overflow:hidden;
        box-shadow:0 10px 30px rgba(0,0,0,.18)}
  .card--front{top:30px}
  .card--back{top:470px;background:var(--white)}

  /* front */
  .front-photo{position:absolute;inset:0;
    background:
      radial-gradient(circle at 76% 22%, var(--sun-glow) 0, rgba(255,240,200,.85) 8%, rgba(230,220,150,.35) 24%, rgba(0,0,0,0) 42%),
      linear-gradient(180deg, #5c7d2e 0%, var(--grass-mid) 40%, var(--grass-dark) 100%);}
  .brand{position:absolute;font-weight:700;letter-spacing:.2em;text-transform:uppercase;white-space:nowrap}
  .card--front .brand{left:44px;top:48px;font-size:24px;color:var(--white)}
  .strap-band{position:absolute;left:0;right:0;top:312px;height:40px;
    background:linear-gradient(90deg,var(--band-orange),var(--band-yellow));
    display:flex;align-items:center;justify-content:center}
  .strapline{color:var(--white);font-size:21px;letter-spacing:.01em;white-space:nowrap}

  /* back */
  .portrait{position:absolute;left:0;top:0;width:300px;height:400px;
    clip-path:polygon(0 0,100% 0,76% 100%,0 100%);
    background:linear-gradient(160deg,#c9b8a4 0%,#8a6e55 40%,#d6a78c 62%,#3c5a6e 100%)}
  .divider{position:absolute;left:0;top:0;width:312px;height:400px;background:var(--white);
    clip-path:polygon(0 0,100% 0,76% 100%,0 100%)}
  .info-bg{position:absolute;left:230px;top:0;right:0;bottom:0;
    clip-path:polygon(82px 0,100% 0,100% 100%,0 100%);
    background:
      radial-gradient(circle at 30% 20%, var(--cream) 0, rgba(255,248,238,0) 60%),
      linear-gradient(160deg,var(--peach-soft) 0%,var(--peach-deep) 100%)}
  .info-panel{position:absolute;left:318px;top:28px;width:356px;height:340px;
    background:rgba(255,250,242,.62)}
  .card--back .brand{left:346px;top:72px;font-size:24px;letter-spacing:.16em;color:var(--brown)}
  .name{position:absolute;left:340px;top:150px;font-size:30px;color:var(--gold);font-weight:400;text-transform:uppercase;letter-spacing:.01em;white-space:nowrap}
  .title{position:absolute;left:340px;top:186px;font-size:20px;color:var(--ink);white-space:nowrap}
  .contacts{position:absolute;left:340px;top:228px;list-style:none}
  .contacts li{display:flex;align-items:center;gap:8px;height:32px;font-size:16px;color:var(--ink);white-space:nowrap}
  .contacts svg{width:15px;height:15px;flex:none}
  .social-mark{width:15px;height:15px;border-radius:3px;background:var(--gold);flex:none}
</style>
</head>
<body>

<section class="card card--front" aria-label="Card front">
  <div class="front-photo" role="img" aria-label="Sunlit close-up of green grass with the sun glowing through trees"></div>
  <div class="brand">Fern Mentoring</div>
  <div class="strap-band"><p class="strapline">A steady guide to help you find clarity in the clutter</p></div>
</section>

<section class="card card--back" aria-label="Card back">
  <div class="info-bg" role="img" aria-label="Soft golden meadow with glowing grass seed heads"></div>
  <div class="info-panel"></div>
  <div class="divider"></div>
  <div class="portrait" role="img" aria-label="Portrait photograph of the coach"></div>

  <div class="brand">Fern Mentoring</div>
  <h1 class="name">Greta Pellham</h1>
  <p class="title">Business &amp; Personal Coach</p>
  <ul class="contacts">
    <li>
      <svg viewBox="0 0 16 16" aria-hidden="true"><path d="M4 1.5l2.2 2.8-1.3 1.6c.9 2 2.4 3.5 4.4 4.4l1.6-1.3 2.8 2.2-1.4 2.3C7 13.5 2.5 9 2 3z" fill="var(--gold)"/></svg>
      +61 (0)458 913307
    </li>
    <li>
      <svg viewBox="0 0 16 16" aria-hidden="true"><rect x="1" y="3" width="14" height="10" rx="1" fill="var(--gold)"/><path d="M1.5 3.6L8 8.6l6.5-5" stroke="var(--white)" stroke-width="1.2" fill="none"/></svg>
      greta@fernmentoring-example.com.au
    </li>
    <li>
      <svg viewBox="0 0 16 16" aria-hidden="true"><circle cx="8" cy="8" r="6.5" fill="none" stroke="var(--gold)" stroke-width="1.5"/><ellipse cx="8" cy="8" rx="2.8" ry="6.5" fill="none" stroke="var(--gold)" stroke-width="1.2"/><path d="M1.5 8h13" stroke="var(--gold)" stroke-width="1.2"/></svg>
      www.fernmentoring-example.com.au
    </li>
    <li>
      <span class="social-mark" aria-hidden="true"></span>
      @fernmentoringAU
    </li>
  </ul>
</section>

</body>
</html>
```